Business Card Design Project

I need a business card designed with these details on the front along with the logo attached on the front.

Address - 217/ 518 Wendlow st Brackfield
Website - www.pellinquarryworks.com.au
Email - dalvin@pellinquarryworks.com.au
Fax - 1900 417 652
Mobile - 0471239058
Telephone - 1300527961
Licence number - 684127k

```html
<!DOCTYPE html>
<html lang="en">
<head>
<meta charset="utf-8">
<title>Pellin Quarryworks – Business Card</title>
<link rel="stylesheet" href="https://fonts.googleapis.com/css2?family=Tinos:wght@400;700&display=swap">
<style>
  :root {
    --page-bg: #f2f2f2;
    --card-red: #e91c24;
    --rule-brown: #4a1e12;
    --card-tan: #c4a07a;
    --tan-soft: #bf946a;
    --ink-brown: #4a2015;
    --tile-cream: #efe6dc;
  }
  * { box-sizing: border-box; margin: 0; padding: 0; }
  html, body {
    width: 1200px;
    height: 900px;
    overflow: hidden;
    background: var(--page-bg);
  }
  body {
    display: flex;
    align-items: center;
    justify-content: center;
    font-family: "Tinos", "Times New Roman", serif;
    color: var(--ink-brown);
  }
  .business-card {
    position: relative;
    width: 900px;
    height: 540px;
    background: var(--card-tan);
    box-shadow: 0 14px 36px rgba(0, 0, 0, 0.22);
    overflow: hidden;
  }
  .card-texture {
    position: absolute;
    inset: 220px 0 0 0;
    background: linear-gradient(160deg, var(--card-tan), var(--tan-soft));
  }
  .header-band {
    position: absolute;
    top: 0;
    left: 0;
    right: 0;
    height: 214px;
    background: var(--card-red);
    border-bottom: 7px solid var(--rule-brown);
  }
  .brand {
    position: absolute;
    left: 300px;
    top: 80px;
    display: flex;
    align-items: center;
    gap: 26px;
  }
  .brand-square {
    width: 100px;
    height: 100px;
    background: var(--tile-cream);
    flex: none;
  }
  .brand-name {
    font-weight: 700;
    font-size: 38px;
    line-height: 1.1;
    letter-spacing: 1px;
    text-transform: uppercase;
    color: var(--ink-brown);
  }
  .contact-list {
    position: absolute;
    left: 48px;
    top: 246px;
    list-style: none;
    font-size: 27px;
    line-height: 44px;
  }
  .contact-label {
    display: inline-block;
    width: 42px;
  }
  .licence {
    position: absolute;
    right: 44px;
    top: 262px;
    font-size: 21px;
  }
</style>
</head>
<body>
  <article class="business-card">
    <div class="card-texture" role="img" aria-label="Tan background with a soft rounded-tile stone pattern"></div>

    <header class="header-band">
      <div class="brand">
        <span class="brand-square"></span>
        <h1 class="brand-name">Pellin<br>Quarryworks</h1>
      </div>
    </header>

    <ul class="contact-list">
      <li><span class="contact-label">A</span>: 217/ 518 Wendlow st Brackfield</li>
      <li><span class="contact-label">W</span>: www.pellinquarryworks.com.au</li>
      <li><span class="contact-label">E</span>: dalvin@pellinquarryworks.com.au</li>
      <li><span class="contact-label">F</span>: 1900 417 652</li>
      <li><span class="contact-label">M</span>: 0471239058</li>
      <li><span class="contact-label">T</span>: 1300527961</li>
    </ul>

    <p class="licence">Licence number - 684127k</p>
  </article>
</body>
</html>
```